Moxy Fen needs some awesome stationary

Do you have what it takes to get my brand? You either do or you don't, have a crack at a design and you my just win my business.

I don't want to waste your or my time, so put your creative genius on either a business card or envelope.

I however need a package of stationary that follows the same brand. I will message you to complete the remaining should I like your first submission.

Here is what I need, have a go!

Basically I need the following for my small business based in melbourne.
- Letterhead (printer ready and MS Word)
- Business Card
- Compliments Slip
- Envelope
- Proposal Cover Page (MS Word only)
- Presentation Folder
- Marbled Fox Cards
- Student Name Tent
- Index Cards
- Vell-Ka

I am establishing the brand and it must be modern, professional but also relaxed; that is not formal and not corporate. It represents a company are leaders, but small enough to care and operate like a bunch of friends. We are bringing people and conversations back to business, and turfing out all the bureaucracy and crazy and wasteful procedures. Its about "lets talk and figure it out together and find even better ways".

Target Market(s)

Mainly companies that build software products, but Agile practices are used in many other industries (even graphic design projects)

Industry/Entity Type

Information Technology

Font styles to use
Sans Serif

Colors
3176b5
aaaaaa

Requirements
Must have
• I like curves and circles and not boxes or rectangles.
• I want a colour rich design with my brand colours, but it must be balanced.
• I want more modern than traditional, but simple modern
Should not have
• Not corporate
• Please don't waste my time if your not going to think about it.
• Don't mess with my primary logo
• Don't change my colours
• Don't overlay logo on image

```html
<!DOCTYPE html>
<html lang="en">
<head>
<meta charset="utf-8">
<title>Moxy Fen — Business Card</title>
<link href="https://fonts.googleapis.com/css2?family=Montserrat:wght@400;600&family=Open+Sans:wght@400;600&display=swap" rel="stylesheet">
<style>
  :root {
    --brand-blue: #3176b5;
    --blue-deep: #0e4d9c;
    --blue-light: #3a78c2;
    --brand-grey: #aaaaaa;
    --paper: #ffffff;
    --backdrop: #e9ebee;
  }
  * { box-sizing: border-box; margin: 0; padding: 0; }
  html, body { width: 1200px; height: 800px; overflow: hidden; }
  body {
    background: var(--backdrop);
    font-family: "Open Sans", Arial, sans-serif;
    position: relative;
  }
  .card {
    position: absolute;
    width: 500px;
    height: 286px;
    border-radius: 4px;
    overflow: hidden;
    box-shadow: 0 6px 18px rgba(20, 40, 70, .18);
  }

  /* Logo side */
  .card-front {
    left: 640px; top: 160px;
    background: linear-gradient(120deg, var(--blue-deep) 0%, var(--blue-light) 100%);
  }
  .card-front .stripe-thick {
    position: absolute; left: 0; right: 0; top: 186px; height: 12px;
    background: var(--paper);
  }
  .card-front .stripe-thin {
    position: absolute; left: 0; right: 0; top: 254px; height: 7px;
    background: var(--paper);
  }
  .brand-mark {
    display: flex; align-items: center; gap: 10px;
    font-family: "Open Sans", Arial, sans-serif;
    font-weight: 600;
  }
  .brand-mark .dot { border-radius: 50%; flex: none; }
  .card-front .brand-mark {
    position: absolute; left: 0; right: 0; top: 78px;
    justify-content: center; color: var(--paper); font-size: 34px;
  }
  .card-front .brand-mark .dot { width: 30px; height: 30px; background: var(--paper); }

  /* Contact side */
  .card-back {
    left: 60px; top: 360px;
    background: linear-gradient(120deg, var(--blue-deep) 0%, var(--blue-light) 100%);
  }
  .card-back .paper-band {
    position: absolute; left: 0; right: 0; top: 0; height: 128px;
    background: var(--paper);
  }
  .card-back .tab {
    position: absolute; left: 118px; width: 18px; height: 9px;
    background: var(--brand-grey);
  }
  .card-back .tab-top { top: 0; }
  .card-back .tab-bottom { top: 128px; background: var(--paper); border: 1px solid #d5d5d5; border-top: 0; }
  .card-back .brand-mark {
    position: absolute; left: 26px; top: 30px;
    color: var(--blue-deep); font-size: 22px; gap: 8px;
  }
  .card-back .brand-mark .dot { width: 22px; height: 22px; background: var(--blue-deep); }

  .name-plate {
    position: absolute; left: 250px; right: 0; top: 92px; height: 56px;
    background: var(--blue-deep);
    color: var(--paper);
    font-family: "Montserrat", Arial, sans-serif;
    font-variant: small-caps;
    text-align: right;
    padding: 7px 20px 0 0;
  }
  .name-plate .person { font-size: 19px; font-weight: 600; letter-spacing: 2px; line-height: 22px; }
  .name-plate .role { font-size: 13px; font-weight: 400; letter-spacing: .5px; line-height: 18px; }

  .contact-list {
    position: absolute; right: 20px; top: 168px;
    list-style: none; color: var(--paper);
    font-size: 11.5px; line-height: 17px; text-align: right;
  }
  .contact-list li { display: flex; justify-content: flex-end; align-items: center; gap: 8px; }
  .contact-list li.lead { font-weight: 600; }
  .contact-list svg { width: 11px; height: 11px; flex: none; }
  .contact-list .spacer { width: 11px; flex: none; }
</style>
</head>
<body>

  <section class="card card-front" aria-label="Business card, logo side">
    <div class="brand-mark"><span class="dot"></span><span>Moxy Fen</span></div>
    <div class="stripe-thick"></div>
    <div class="stripe-thin"></div>
  </section>

  <section class="card card-back" aria-label="Business card, contact side">
    <div class="paper-band"></div>
    <div class="tab tab-top"></div>
    <div class="tab tab-bottom"></div>
    <div class="brand-mark"><span class="dot"></span><span>Moxy Fen</span></div>

    <div class="name-plate">
      <div class="person">Dara Colvin</div>
      <div class="role">CEO, Professional Scrum Trainer</div>
    </div>

    <ul class="contact-list">
      <li class="lead">1300MOXYFEN
        <svg viewBox="0 0 12 12" aria-hidden="true"><path fill="#fff" d="M1 4c0-2 2-3 5-3s5 1 5 3l-2 1-1-1.5H4L3 5zM3 6h6l1.5 5h-9z"/></svg>
      </li>
      <li>+61 400 218 735
        <svg viewBox="0 0 12 12" aria-hidden="true"><rect x="3.5" y="1" width="5" height="10" rx="1" fill="none" stroke="#fff" stroke-width="1.2"/></svg>
      </li>
      <li>dara@moxyfen.com.au
        <svg viewBox="0 0 12 12" aria-hidden="true"><rect x="1" y="2.5" width="10" height="7" fill="none" stroke="#fff" stroke-width="1.1"/><path d="M1 2.5l5 4 5-4" fill="none" stroke="#fff" stroke-width="1.1"/></svg>
      </li>
      <li>www.moxyfen.com.au
        <svg viewBox="0 0 12 12" aria-hidden="true"><circle cx="6" cy="6" r="5" fill="none" stroke="#fff" stroke-width="1"/><ellipse cx="6" cy="6" rx="2.2" ry="5" fill="none" stroke="#fff" stroke-width="1"/><path d="M1 6h10" stroke="#fff" stroke-width="1"/></svg>
      </li>
      <li>PO Box 1180, Elmvale North,<span class="spacer"></span></li>
      <li>VIC 3999, Australia
        <svg viewBox="0 0 12 12" aria-hidden="true"><path fill="#fff" d="M6 11C3 7.5 2.5 6 2.5 4.5a3.5 3.5 0 0 1 7 0C9.5 6 9 7.5 6 11zm0-5a1.5 1.5 0 1 0 0-3 1.5 1.5 0 0 0 0 3z"/></svg>
      </li>
    </ul>
  </section>

</body>
</html>
```